Business card for Eyelash extension salon in Alder Heights,California USA

We need new business card for our salon in Alder Heights. The salon name is 'Lashvera' . We would like to have...Business name: Lashvera Name of person: will provide later Address 4720 N.Alder Crest Ave Alder Heights , CA 90477 Phone: will provide later (Text only) Web: www.lashverastudio.example Snapgrid icon, Circlebook icon follow us for seasonal campaign and news @lashverastudiolounge Design should look elegant, high-end, clean, simple, cohesive with my brand. Please refer my brand board. Business name color will be metallic bronzy color. Im thinking grey background or white background. Thanks

Target Market(s)

25-35. Gender neutral. People who are in Entertainment business industry.
This is High-end Eyelash extension salon in Alder Heights

Industry/Entity Type

Beauty Salon

Contact Information for Business Card

Business name: Lashvera
Name of person: will provide later
Address 4720 N.Alder Crest Ave Alder Heights , CA 90477
Phone: will provide later (Text only)
Web: www.lashverastudio.example
Snapgrid icon, Circlebook icon
follow us for seasonal campaign and news @lashverastudiolounge

Requirements
Must have
• Beautiful, elegant, clean and simple look but very attractive and modern
Should not have
• We don't like too clutter, too busy designs.

```html
<!DOCTYPE html>
<html lang="en">
<head>
<meta charset="UTF-8">
<title>Lashvera Business Card</title>
<link rel="stylesheet" href="https://fonts.googleapis.com/css2?family=Lato:ital,wght@0,300;0,400;1,700&family=Arimo:wght@700&display=swap">
<style>
  :root {
    --stage: #9b9b9b;
    --card-white: #ffffff;
    --bronze: #8b6750;
    --bronze-text: #7a5641;
    --ink: #2f2f2f;
    --rule: #cfcfcf;
    --rule-light: rgba(255,255,255,0.35);
    --on-bronze: #ffffff;
  }
  * { margin: 0; padding: 0; box-sizing: border-box; }
  html, body { width: 1200px; height: 900px; overflow: hidden; }
  body {
    background: var(--stage);
    font-family: "Lato", sans-serif;
    position: relative;
  }
  .card {
    position: absolute;
    width: 478px;
    height: 295px;
    box-shadow: 3px 4px 6px rgba(0,0,0,0.4);
    overflow: hidden;
  }
  .card--front {
    left: 120px; top: 275px;
    background: var(--card-white);
    border-radius: 0 52px 0 52px;
  }
  .card--back {
    left: 607px; top: 273px;
    background: var(--bronze);
    border-radius: 52px 0 52px 0;
  }
  .brand {
    position: absolute;
    font-family: "Lato", sans-serif;
    font-weight: 300;
    line-height: 1;
    white-space: nowrap;
  }
  .brand__tagline {
    position: absolute;
    font-size: 7px;
    letter-spacing: 1.6px;
    white-space: nowrap;
  }
  .card--front .brand {
    right: 33px; top: 82px;
    font-size: 44px;
    color: var(--bronze-text);
  }
  .card--front .brand__tagline {
    right: 62px; top: 155px;
    color: var(--bronze-text);
  }
  .card--back .brand {
    left: 0; width: 478px; top: 92px;
    text-align: center;
    font-size: 60px;
    color: var(--on-bronze);
  }
  .card--back .brand__tagline {
    left: 234px; top: 182px;
    font-size: 8.5px;
    color: var(--on-bronze);
  }
  .holder {
    position: absolute;
    left: 30px; top: 201px;
    right: 27px;
    display: flex;
    align-items: center;
    gap: 8px;
  }
  .holder__name {
    font-family: "Arimo", sans-serif;
    font-weight: 700;
    font-size: 16px;
    letter-spacing: 0.3px;
    color: var(--bronze-text);
    white-space: nowrap;
  }
  .holder__rule { flex: 1; height: 1px; background: var(--rule); }
  .contact {
    position: absolute;
    left: 30px; top: 231px;
    font-size: 13px;
    line-height: 18px;
    color: var(--ink);
    list-style: none;
  }
  .contact li { display: flex; align-items: center; gap: 4px; white-space: nowrap; }
  .contact svg { width: 11px; height: 11px; fill: var(--bronze-text); }
  .address {
    position: absolute;
    right: 27px; top: 231px;
    font-size: 13px;
    line-height: 18px;
    color: var(--ink);
    text-align: right;
    font-style: normal;
    white-space: nowrap;
  }
  .social {
    position: absolute;
    left: 49px; right: 57px; top: 223px;
    display: flex;
    align-items: center;
    gap: 8px;
  }
  .social__rule { flex: 1; height: 1px; background: var(--rule-light); }
  .social__item {
    display: flex; align-items: center; gap: 4px;
    font-size: 11px;
    color: var(--on-bronze);
  }
  .social__dot {
    width: 12px; height: 12px; border-radius: 50%;
    background: var(--on-bronze);
  }
  .follow {
    position: absolute;
    left: 0; width: 472px; top: 249px;
    text-align: center;
    font-size: 13px;
    color: var(--on-bronze);
    white-space: nowrap;
  }
  .follow__handle { font-weight: 700; font-style: italic; }
</style>
</head>
<body>
  <section class="card card--front" aria-label="Card front">
    <div class="brand">Lashvera</div>
    <div class="brand__tagline">ALDER HEIGHTS</div>
    <div class="holder">
      <span class="holder__name">DANIEL HARWOOD</span>
      <span class="holder__rule"></span>
    </div>
    <ul class="contact">
      <li>
        <svg viewBox="0 0 24 24" aria-hidden="true"><path d="M6.6 10.8a15 15 0 0 0 6.6 6.6l2.2-2.2a1 1 0 0 1 1-.25 11.4 11.4 0 0 0 3.6.57 1 1 0 0 1 1 1V20a1 1 0 0 1-1 1A17 17 0 0 1 3 4a1 1 0 0 1 1-1h3.5a1 1 0 0 1 1 1c0 1.25.2 2.450.57 3.57a1 1 0 0 1-.25 1z"/></svg>
        044-555 010 247
      </li>
      <li>
        <svg viewBox="0 0 24 24" aria-hidden="true"><circle cx="12" cy="12" r="10"/></svg>
        www.lashverastudio.example
      </li>
    </ul>
    <address class="address">4720 N.Alder Crest<br>Ave Alder Heights , CA 90477</address>
  </section>

  <section class="card card--back" aria-label="Card back">
    <div class="brand">Lashvera</div>
    <div class="brand__tagline">ALDER HEIGHTS</div>
    <div class="social">
      <span class="social__rule"></span>
      <span class="social__item"><span class="social__dot"></span>Circlebook</span>
      <span class="social__item"><span class="social__dot"></span>Snapgrid</span>
      <span class="social__rule"></span>
    </div>
    <p class="follow">Follow us for seasonal campaign and news <span class="follow__handle">@lashverastudiolounge</span></p>
  </section>
</body>
</html>
```